Brightlane Rapid Rinse Web Design

We are looking for a web design that highlights our state of the art fully automated commercial vehicle washing equipment. Similar system to a car wash however this system is meant for the largest vehicles on our roadways. Transport trucks with or without a trailer, busses both highway and school, RV's from 5th wheel type to A Class. Cement trucks, dump trucks, vac trucks, fuel trucks etc. Pick ups with utility trailers...Refrigerator truck clean outs.
Brightlane Rapid Rinse will wash your vehicle quickly and with a minimal impact on the environment

Home page
About us
Why Brightlane
Services and pricing
Videos of wash system
Fleets
contact us

Target Market(s)

Commercial vehicle owners and operators as well as corporate fleets. Includes busses, municipal, school and highway.both school and

Industry/Entity Type

transportation

Coding

Coded - Design and coding required

Number of Pages Required

5+ page

Font styles to use
Sans Serif

Colors
0054AA
0677BA
7BADD7
CADEEF
E8F1F8

Requirements
Must have
• Welcome page,why us page which describes the financial and environmental benefits. payment processing page, contact us page, Services which is washing vehicles and greasing for commercial vehicles that want that service and grease
Nice to have
• pictures of both clean and dirty commercial vehicles ie. before and after

```html
<!DOCTYPE html>
<html lang="en">
<head>
<meta charset="utf-8">
<title>Brightlane Rapid Rinse</title>
<link rel="stylesheet" href="https://fonts.googleapis.com/css2?family=Cinzel:wght@600;700&family=Roboto:wght@400;500;700&display=swap">
<style>
:root{
  --navy:#03032e;
  --blue:#0677ba;
  --deep-blue:#0054aa;
  --sky:#7badd7;
  --mist:#cadeef;
  --ice:#e8f1f8;
  --white:#ffffff;
  --ink:#111122;
  --grey:#666677;
}
*{box-sizing:border-box;margin:0;padding:0}
html,body{width:1200px;height:2473px;overflow:hidden}
body{font-family:"Roboto",sans-serif;color:var(--ink);background:var(--white);position:relative}
.heading{font-family:"Cinzel",serif;font-weight:700;line-height:1.08}
.wrap{position:absolute;left:143px;width:914px}

/* header */
.site-header{position:absolute;top:0;left:0;width:1200px;height:86px;background:var(--navy)}
.brand{position:absolute;left:142px;top:10px;color:var(--blue);font-weight:700}
.brand-name{font-size:27px;letter-spacing:0.5px;line-height:30px}
.brand-tag{font-size:16px;letter-spacing:5.5px;line-height:22px}
.main-nav{position:absolute;left:372px;top:52px;display:flex;gap:21px}
.main-nav a{color:var(--white);font-size:11px;font-weight:700;text-decoration:none;text-transform:uppercase;position:relative;letter-spacing:-0.1px}
.main-nav a.active::before{content:"";position:absolute;left:0;right:0;top:-7px;height:2px;background:var(--blue)}
.social{display:flex;gap:7px}
.social span{width:25px;height:25px;border-radius:50%;background:var(--white);border:2px solid var(--sky);display:block}
.site-header .social{position:absolute;left:904px;top:15px}

/* hero */
.hero{position:absolute;top:86px;left:0;width:1200px;height:524px;background:linear-gradient(180deg,#6e5a74 0%,#8d8a95 30%,#b9b8bd 60%,#8e8e92 100%)}
.hero-box{position:absolute;left:514px;top:155px;width:542px;height:224px;background:var(--blue);border:3px solid var(--white);padding:24px 0 0 48px}
.hero-title{color:var(--white);font-size:58px;line-height:60px}
.hero-sub{color:var(--white);font-size:26px;font-weight:500;margin-top:14px}
.hero-actions{position:absolute;left:566px;top:357px;display:flex;gap:11px}
.btn{display:inline-block;font-size:13px;font-weight:700;text-transform:uppercase;padding:0 17px;height:40px;line-height:40px;text-decoration:none}
.btn-dark{background:var(--navy);color:var(--white)}
.btn-light{background:var(--white);color:var(--navy);padding:0 20px}
.btn-blue{background:var(--blue);color:var(--white);padding:0 23px}
.slider-dots{position:absolute;left:1116px;top:262px;display:flex;flex-direction:column;gap:11px}
.slider-dots span{width:8px;height:8px;border-radius:50%;background:var(--white)}
.slider-dots span.on{background:var(--blue)}

/* mission */
.mission{position:absolute;top:610px;left:0;width:1200px;height:195px;background:var(--navy)}
.mission .heading{position:absolute;left:144px;top:38px;color:var(--white);font-size:56px;line-height:61px}
.mission p{position:absolute;left:590px;top:62px;width:470px;color:var(--white);font-size:16px;line-height:26px}

/* services */
.services{position:absolute;top:805px;left:0;width:1200px;height:625px;background:var(--blue)}
.section-title{position:absolute;left:0;width:1200px;text-align:center;font-size:58px}
.services .section-title{top:72px;color:var(--white)}
.card-photo{position:absolute;top:170px;width:293px;height:243px}
.card{position:absolute;top:352px;width:260px;height:192px;background:var(--white);text-align:center;padding-top:22px;box-shadow:0 8px 24px rgba(0,0,0,0.2)}
.card h3{font-size:18px;font-weight:500;color:var(--ink)}
.card p{font-size:12px;line-height:17.5px;color:var(--grey);margin:10px auto 16px;width:200px}
.card .btn{height:40px;line-height:40px;font-size:13px}
.card.featured{background:var(--navy)}
.card.featured h3,.card.featured p{color:var(--white)}

/* gallery */
.gallery-title{top:1512px;color:var(--ink)}
.gallery-title .accent{color:var(--blue)}
.gallery-photo{position:absolute;top:1618px;width:445px;height:285px}
.arrow{position:absolute;top:1738px;width:45px;height:45px}

/* environment */
.environment{position:absolute;top:1937px;left:0;width:1200px;height:291px;background:linear-gradient(180deg,#f7f9fb 0%,var(--ice) 45%,var(--mist) 100%)}
.environment .heading{position:absolute;left:143px;top:88px;font-size:58px;line-height:62px;color:var(--ink)}
.environment .heading .accent{color:var(--blue)}
.env-text{position:absolute;left:690px;top:100px;width:370px}
.env-text h3{font-size:19px;font-weight:500;color:var(--ink)}
.env-text p{font-size:15px;line-height:26px;color:var(--grey);margin-top:6px}

/* footer */
.site-footer{position:absolute;top:2228px;left:0;width:1200px;height:245px;background:var(--navy);text-align:center;color:var(--white)}
.site-footer .social{position:absolute;left:492px;top:65px;gap:8px}
.site-footer .social span{width:37px;height:37px}
.footer-nav{position:absolute;top:130px;left:0;width:1200px;display:flex;justify-content:center;gap:27px}
.footer-nav a{color:var(--white);font-size:14px;font-weight:700;text-decoration:none;text-transform:uppercase}
.copyright{position:absolute;top:176px;left:0;width:1200px;font-size:14px}
</style>
</head>
<body>

<header class="site-header">
  <div class="brand">
    <div class="brand-name">Brightlane</div>
    <div class="brand-tag">RAPID RINSE</div>
  </div>
  <nav class="main-nav">
    <a class="active" href="#">Home</a>
    <a href="#">About Us</a>
    <a href="#">Why Brightlane</a>
    <a href="#">Services and Pricing</a>
    <a href="#">Videos of Wash System</a>
    <a href="#">Fleets</a>
    <a href="#">Contact Us</a>
  </nav>
  <div class="social" aria-label="Social links"><span></span><span></span><span></span><span></span><span></span></div>
</header>

<section class="hero" role="img" aria-label="Photo of a white truck inside an automated wash bay with red and black brushes">
  <div class="hero-box">
    <h1 class="heading hero-title">Brightlane<br>Rapid Rinse</h1>
    <div class="hero-sub">LESS THAN 15 MINUTES</div>
  </div>
  <div class="hero-actions">
    <a class="btn btn-dark" href="#">Book a Wash</a>
    <a class="btn btn-light" href="#">Learn More</a>
    <a class="btn btn-dark" href="#">Contact Us</a>
  </div>
  <div class="slider-dots"><span></span><span class="on"></span><span></span></div>
</section>

<section class="mission">
  <h2 class="heading">Mission<br>Statement</h2>
  <p>A concise statement about our dedication to revolutionizing truck washing with advanced technology and sustainable practices, set against a dark blue backdrop.</p>
</section>

<section class="services">
  <h2 class="heading section-title">Services</h2>

  <div class="card-photo" style="left:144px;background:linear-gradient(180deg,#5e6a6c,#c9cdd0 55%,#7c8284)" role="img" aria-label="Photo of a white truck being washed between green brushes"></div>
  <div class="card-photo" style="left:453px;background:linear-gradient(160deg,#2b1a14,#7a4a30 50%,#1e1612)" role="img" aria-label="Photo of a mechanic servicing an engine"></div>
  <div class="card-photo" style="left:762px;background:linear-gradient(180deg,#0b2fa0,#3a55b8 50%,#1a2f8a)" role="img" aria-label="Photo of a white van under blue wash brushes"></div>

  <div class="card" style="left:161px">
    <h3>Automated Truck Wash</h3>
    <p>Sed ut perspiciatis unde omnis iste natus error sit voluptatem usantium doloremque laudantium, totam rem aperiam, eaque ipsa quae</p>
    <a class="btn btn-blue" href="#">Read More</a>
  </div>
  <div class="card featured" style="left:470px">
    <h3>Additional Services</h3>
    <p>Sed ut perspiciatis unde omnis iste natus error sit voluptatem usantium doloremque laudantium, totam rem aperiam, eaque ipsa quae</p>
    <a class="btn btn-blue" href="#">Read More</a>
  </div>
  <div class="card" style="left:779px">
    <h3>Fleet Services</h3>
    <p>Sed ut perspiciatis unde omnis iste natus error sit voluptatem usantium doloremque laudantium, totam rem aperiam, eaque ipsa quae</p>
    <a class="btn btn-blue" href="#">Read More</a>
  </div>
</section>

<h2 class="heading section-title gallery-title"><span class="accent">Our</span> Gallery</h2>
<div class="gallery-photo" style="left:146px;background:linear-gradient(135deg,#c98a3a,#6b4424 50%,#2d2a26)" role="img" aria-label="Photo of a muddy off-road vehicle wheel at sunset"></div>
<div class="gallery-photo" style="left:610px;background:linear-gradient(135deg,#1b2c4d,#2f5f9c 50%,#9aa7b8)" role="img" aria-label="Photo of a blue semi truck driving at night"></div>
<svg class="arrow" style="left:77px" viewBox="0 0 45 45" aria-label="Previous"><circle cx="22.5" cy="22.5" r="21.5" fill="#fff" stroke="#555" stroke-width="1"/><path d="M26 14 L18 22.5 L26 31" fill="none" stroke="#333" stroke-width="2"/></svg>
<svg class="arrow" style="left:1079px" viewBox="0 0 45 45" aria-label="Next"><circle cx="22.5" cy="22.5" r="21.5" fill="#fff" stroke="#555" stroke-width="1"/><path d="M19 14 L27 22.5 L19 31" fill="none" stroke="#333" stroke-width="2"/></svg>

<section class="environment" role="img" aria-label="Soft background photo of a glass globe over water">
  <h2 class="heading"><span class="accent">Environmental</span><br>Responsibility</h2>
  <div class="env-text">
    <h3>Commitment to Sustainability</h3>
    <p>A section dedicated to our eco-friendly practices, such as our proprietary water reclamation and energy efficiency system, including space for infographics to convey our dedication to the environment.</p>
  </div>
</section>

<footer class="site-footer">
  <div class="social" aria-label="Social links"><span></span><span></span><span></span><span></span><span></span></div>
  <nav class="footer-nav">
    <a href="#">Home</a>
    <a href="#">About Us</a>
    <a href="#">Why Brightlane</a>
    <a href="#">Services and Pricing</a>
    <a href="#">Videos of Wash System</a>
    <a href="#">Fleets</a>
    <a href="#">Contact Us</a>
  </nav>
  <div class="copyright">© 2024 Brightlane Rapid Rinse All rights reserved.Privacy &nbsp;|&nbsp; Terms of Use</div>
</footer>

</body>
</html>
```